Business Card and Letterhead for Pimlu - modern real estate business

I need a double sided business card design for Pimlu. Please see business card brief here https://files.trelvonadocs.com/sheet/r/7QzTmWbaXLJnoPEd-kRyUgFhHsstbvCe2qfoMxDa_pz/view?mode=shared

Please feel free to design the business cards however you feel best. I am happy to give some creative freedoms and then provide feedback from there.

Please then also create a letterhead to match the business card design

Colors

Designer to choose colors to be used in the design.

Requirements
Must have
• Must be a modern, elegant business card which looks very professional

```html
<!DOCTYPE html>
<html lang="en">
<head>
<meta charset="utf-8">
<title>Pimlu Business Card</title>
<link rel="stylesheet" href="https://fonts.googleapis.com/css2?family=Montserrat:wght@400;500;700&display=swap">
<style>
  :root {
    --brand-red: #e3051b;
    --brand-red-deep: #c90416;
    --ink: #1e1e1e;
    --paper: #ffffff;
    --backdrop: #eceae7;
    --photo-light: #d9d9d9;
    --photo-dark: #55585c;
  }
  * { box-sizing: border-box; margin: 0; padding: 0; }
  html, body {
    width: 1200px;
    height: 800px;
    overflow: hidden;
    background: var(--backdrop);
    font-family: "Montserrat", Arial, sans-serif;
  }
  .canvas {
    position: relative;
    width: 1200px;
    height: 800px;
  }
  .card {
    position: absolute;
    top: 241px;
    width: 520px;
    height: 318px;
    overflow: hidden;
    box-shadow: 0 6px 18px rgba(0,0,0,0.18);
  }
  .card--front {
    left: 60px;
    background: var(--brand-red);
    display: flex;
    align-items: center;
    justify-content: center;
  }
  .front-wordmark {
    font-weight: 700;
    font-size: 92px;
    letter-spacing: 4px;
    color: var(--brand-red-deep);
  }
  .card--back {
    left: 620px;
    background: var(--paper);
  }
  .back-wordmark {
    position: absolute;
    left: 170px;
    top: 22px;
    font-weight: 700;
    font-size: 60px;
    letter-spacing: 3px;
    color: var(--brand-red);
    line-height: 1;
  }
  .agent {
    position: absolute;
    left: 34px;
    top: 104px;
    width: 230px;
  }
  .agent-name {
    font-weight: 700;
    font-size: 20px;
    color: var(--brand-red);
    text-transform: uppercase;
    letter-spacing: 0.5px;
  }
  .agent-title {
    font-weight: 500;
    font-size: 14px;
    color: var(--ink);
    margin-top: 2px;
  }
  .rule {
    width: 86px;
    height: 2px;
    background: var(--brand-red);
    margin: 8px 0 10px;
  }
  .contact-list { list-style: none; }
  .contact-item {
    display: flex;
    align-items: center;
    gap: 7px;
    font-size: 13.5px;
    color: var(--ink);
    line-height: 19px;
  }
  .contact-icon { width: 11px; height: 11px; flex: none; }
  .address {
    font-size: 13.5px;
    color: var(--ink);
    line-height: 19px;
  }
  .agent-photo {
    position: absolute;
    right: 40px;
    bottom: 0;
    width: 230px;
    height: 228px;
    background: linear-gradient(180deg, var(--photo-light) 0%, var(--photo-dark) 100%);
    border-radius: 110px 110px 0 0;
  }
  .base-band {
    position: absolute;
    left: 0;
    bottom: 0;
    width: 252px;
    height: 8px;
    background: var(--brand-red);
  }
</style>
</head>
<body>
  <main class="canvas">
    <section class="card card--front" aria-label="Business card front">
      <span class="front-wordmark">PIMLU</span>
    </section>

    <section class="card card--back" aria-label="Business card back">
      <div class="back-wordmark">PIMLU</div>

      <div class="agent">
        <h1 class="agent-name">Reid Callan</h1>
        <p class="agent-title">Licenced Real Estate Agent</p>
        <div class="rule"></div>
        <ul class="contact-list">
          <li class="contact-item">
            <svg class="contact-icon" viewBox="0 0 12 12" aria-hidden="true"><path d="M2.5 1 L4.5 1 L5.3 3.6 L4 4.6 Q5.2 7 7.4 8 L8.4 6.7 L11 7.5 L11 9.5 Q10.5 11 9 11 Q1 10 1 3 Q1 1.5 2.5 1Z" fill="#e3051b"/></svg>
            0400 555 182
          </li>
          <li class="contact-item">
            <svg class="contact-icon" viewBox="0 0 12 12" aria-hidden="true"><rect x="0.5" y="2" width="11" height="8" fill="#e3051b"/><path d="M0.5 2 L6 6.5 L11.5 2" fill="none" stroke="#fff" stroke-width="1"/></svg>
            reid@pimlu.com
          </li>
          <li class="contact-item">
            <svg class="contact-icon" viewBox="0 0 12 12" aria-hidden="true"><circle cx="6" cy="6" r="5.5" fill="#e3051b"/><path d="M0.5 6 H11.5 M6 0.5 V11.5 M6 0.5 Q2.5 6 6 11.5 M6 0.5 Q9.5 6 6 11.5" fill="none" stroke="#fff" stroke-width="0.8"/></svg>
            www.pimlu.com
          </li>
        </ul>
        <div class="rule"></div>
        <p class="address">PO Box 7130<br>Larkford NSW 2790</p>
      </div>

      <div class="agent-photo" role="img" aria-label="Portrait photograph of the agent in a dark suit"></div>
      <div class="base-band"></div>
    </section>
  </main>
</body>
</html>
```